Tall ridge firewood

It a new firewood outlet in Jindabyne nsw that will only sell top hardwood firewood (ironbark , red gum, grey gum, an box mix. I would like to see a web page the we can do order online payment for delivery. It will all so need to have photos of the firewood. I all so have logo for tall ridge firewood
Must have a modem look but easy to use I would like to see a black back ground of some sort.

Here are some other firewood web pages for ideas and firewood info
http://www.example-logpile.com.au
http://www.example-stackwood.com.au
http://www.example-splitlog.com.au
http://www.example-kendaltimber.com.au/firewood

Industry/Entity Type

Firewood

```html
<!DOCTYPE html>
<html lang="en">
<head>
<meta charset="utf-8">
<title>Tall ridge firewood</title>
<link href="https://fonts.googleapis.com/css2?family=Oswald:wght@500;700&family=Open+Sans:wght@400;600;700&display=swap" rel="stylesheet">
<style>
:root{
  --blue:#1f6fc0;
  --blue-dark:#165ba3;
  --blue-nav:#2a78c9;
  --black:#111;
  --ink:#222;
  --grey-text:#6b6b6b;
  --panel-grey:#efefef;
  --tan:#c7a072;
  --red:#d0201b;
  --wood-dark:#3a2414;
  --wood-mid:#8a5a34;
  --white:#fff;
}
*{box-sizing:border-box;margin:0;padding:0}
html,body{width:814px;height:1200px;overflow:hidden}
body{position:relative;font-family:"Open Sans",Arial,sans-serif;background:var(--black);color:var(--ink)}
.display{font-family:"Oswald","Arial Narrow",sans-serif;font-weight:700;text-transform:uppercase}
.abs{position:absolute}

/* header */
.site-header{left:0;top:0;width:814px;height:54px;background:linear-gradient(90deg,#2a180d,#4a2d18 50%,#2a180d)}
.brand{left:117px;top:12px;color:var(--white);font-size:20px;letter-spacing:.5px;line-height:1}
.brand-tag{left:118px;top:35px;color:#e8e8e8;font-size:6.5px;letter-spacing:.2px}
.call{right:117px;top:11px;text-align:right;color:var(--white)}
.call small{display:block;font-family:"Oswald",sans-serif;font-size:7px;font-weight:700}
.call .phone{font-family:"Oswald",sans-serif;font-weight:700;font-size:15px;display:flex;align-items:center;gap:4px}

/* nav */
.main-nav{left:0;top:54px;width:814px;height:36px;background:var(--blue-nav)}
.main-nav ul{position:absolute;left:117px;top:0;width:580px;height:36px;display:flex;list-style:none;background:var(--blue-dark)}
.main-nav li{height:36px;display:flex;align-items:center;justify-content:center;color:var(--white);font-size:14px;border-right:1px solid rgba(255,255,255,.2)}
.main-nav li.active{background:var(--black)}

/* hero */
.hero{left:0;top:90px;width:814px;height:293px;background:radial-gradient(circle at 30% 40%,#a06a3c,#6b4223 45%,#2e1a0d 100%)}
.hero-title{left:117px;top:175px;color:var(--white);font-size:35px;line-height:34px;letter-spacing:-.3px;text-shadow:0 2px 3px rgba(0,0,0,.5)}
.hero-figure{left:412px;top:112px;width:312px;height:271px;border-radius:140px 140px 0 0;background:linear-gradient(160deg,#2f6fb8,#1d4f8a 60%,#5a3a22)}
.slide-arrow{top:190px;width:37px;height:58px;border:1px solid rgba(255,255,255,.6);background:rgba(0,0,0,.25);display:flex;align-items:center;justify-content:center}
.slide-arrow.prev{left:0}
.slide-arrow.next{right:0}

/* welcome */
.welcome{left:0;top:383px;width:814px;height:333px;background:var(--panel-grey)}
.welcome-title{left:117px;top:410px;font-size:18px;color:var(--black)}
.welcome-title span{color:var(--blue)}
.video-thumb{left:116px;top:454px;width:159px;height:127px;border-radius:2px;background:radial-gradient(circle at 50% 55%,#e0561d,#7a2b10 35%,#2a1d18 70%)}
.play{left:176px;top:500px}
.lead{left:288px;top:453px;width:212px;font-size:10.2px;line-height:13.4px;color:var(--ink);text-align:justify}
.body-copy{font-size:8.7px;line-height:11.6px;color:var(--grey-text);text-align:justify}
.body-a{left:288px;top:527px;width:212px}
.body-b{left:116px;top:590px;width:384px}

/* order form */
.order{left:528px;top:340px;width:169px;height:340px;background:var(--tan);box-shadow:0 2px 4px rgba(0,0,0,.2)}
.order-head{height:43px;background:var(--blue);color:#cfe0f3;font-size:17px;display:flex;align-items:center;justify-content:center}
.order-intro{position:absolute;left:19px;top:54px;width:135px;font-size:7px;line-height:9.6px;color:#4a3520}
.order-intro b{color:#2a1a0c}
.field{position:absolute;left:19px;width:130px;height:17px;background:var(--white);border:1px solid #b08a5e;font-size:6.6px;color:#888;padding-left:8px;line-height:15px}
.field i{color:var(--red);font-style:normal}
.field.select::after{content:"";position:absolute;right:0;top:-1px;width:8px;height:17px;background:#1a1a1a}
.field.select::before{content:"";position:absolute;right:2px;top:7px;border:2px solid transparent;border-top-color:#fff;z-index:1}
.next-btn{position:absolute;left:19px;top:288px;width:132px;height:34px;background:var(--blue);color:var(--white);font-size:20px;display:flex;align-items:center;justify-content:center;gap:7px}

/* products */
.products{left:0;top:716px;width:814px;height:234px;background:linear-gradient(#fff,#f4f4f4)}
.products-title{left:0;top:743px;width:814px;text-align:center;font-size:18px;color:var(--blue)}
.products-title span{color:var(--black)}
.product{top:794px;width:139px;text-align:center}
.product .photo{height:82px;margin-bottom:9px}
.product h3{font-size:9px;font-weight:400;color:var(--ink)}
.product small{display:block;font-size:5.5px;color:#888;margin-top:1px}
.product .price{font-size:10px;font-weight:700;color:var(--red)}
.carousel-btn{top:826px;width:17px;height:17px;border-radius:50%;background:#8a8a8a;display:flex;align-items:center;justify-content:center}

/* footer */
.site-footer{left:0;top:950px;width:814px;height:250px;background:radial-gradient(circle at 50% 40%,#3a1a10,#160c08 60%,#0b0706)}
.foot-title{top:984px;font-size:12px;color:var(--blue-nav)}
.foot-links{top:1012px;list-style:none;font-size:7.5px;color:var(--white)}
.foot-links li{height:13.6px;width:64px;border-bottom:1px solid rgba(255,255,255,.12);line-height:12px}
.hotline{left:392px;top:1012px;color:var(--white);font-size:11.5px;line-height:15px}
.areas{left:392px;top:1045px;width:150px;font-size:5.7px;line-height:10px;color:#9a9a9a}
.hours{left:586px;top:1012px;list-style:none;font-size:7.5px;color:var(--white);line-height:13.6px}
.foot-brand{left:357px;top:1100px;width:100px;text-align:center}
.foot-brand .dot{width:44px;height:44px;border-radius:50%;background:var(--white);margin:0 auto 2px}
.foot-brand p{font-family:"Oswald",sans-serif;font-weight:700;font-size:8px;color:var(--blue-nav);text-transform:uppercase}
.copyright{left:0;top:1166px;width:814px;text-align:center;font-size:7.5px;color:#ccc}
</style>
</head>
<body>

<header class="site-header abs">
  <div class="brand display abs">Tall ridge firewood</div>
  <div class="brand-tag abs">WOOD THAT GETS YOU HOT AND LAST ALL NIGHT LONG</div>
  <div class="call abs">
    <small>CALL US NOW</small>
    <div class="phone">
      <svg width="8" height="12" viewBox="0 0 8 12"><rect x="0.8" y="0.8" width="6.4" height="10.4" rx="1" fill="none" stroke="#f0a020" stroke-width="1.4"/><circle cx="4" cy="9.4" r=".7" fill="#f0a020"/></svg>
      (02) 5550 1847
    </div>
  </div>
</header>

<nav class="main-nav abs">
  <ul class="display">
    <li class="active" style="width:74px">Home</li>
    <li style="width:96px">About us</li>
    <li style="width:128px">Our products</li>
    <li style="width:118px">Order online</li>
    <li style="width:56px">FAQ</li>
    <li style="width:108px;border-right:0">Contact us</li>
  </ul>
</nav>

<section class="hero abs" role="img" aria-label="Photograph of stacked hardwood log ends"></section>
<h1 class="hero-title display abs">Delivering top<br>quality seasoned<br>hardwood all<br>year round</h1>
<div class="hero-figure abs" role="img" aria-label="Illustrated lumberjack mascot carrying an axe"></div>
<div class="slide-arrow prev abs"><svg width="14" height="20" viewBox="0 0 14 20"><path d="M11 2 3 10l8 8" fill="none" stroke="#fff" stroke-width="3"/></svg></div>
<div class="slide-arrow next abs"><svg width="14" height="20" viewBox="0 0 14 20"><path d="M3 2l8 8-8 8" fill="none" stroke="#fff" stroke-width="3"/></svg></div>

<section class="welcome abs"></section>
<h2 class="welcome-title display abs">Welcome <span>to our new online store</span></h2>
<div class="video-thumb abs" role="img" aria-label="Video still of a fire burning in a wood heater"></div>
<svg class="play abs" width="39" height="39" viewBox="0 0 39 39"><circle cx="19.5" cy="19.5" r="17.5" fill="#1f6fc0" stroke="#fff" stroke-width="3"/><path d="M15 11.5v16l12-8z" fill="#fff"/></svg>
<p class="lead abs">This is Mockup Studio's version &nbsp;of Lorem Ipsum. Proin gravida nibh vel velit auctor aliquet. Aenean sollicitudin, lorem quis bibendum auctor, nisi elit consequat ipsum, nec sagittis sem nibh id elit.</p>
<p class="body-copy body-a abs">This is Mockup Studio's version of Lorem Ipsum. Proin gravida nibh vel velit auctor aliquet. Aenean sollicitudin, lorem quis bibendum auctor, nisi elit consequat ipsum, nec sagittis sem nibh id elit. Duis sed odio sit amet nibh vulputate cursus a sit amet</p>
<p class="body-copy body-b abs">tincidunt auctor a ornare odio. Sed non mauris vitae erat consequat auctor eu in elit. Class aptent taciti sociosqu ad litora torquent per conubia nostra, per inceptos himenaeos. Mauris in erat justo. Nullam ac urna eu felis dapibus condimentum sit amet a augue. Sed non neque elit. Sed ut imperdiet nisi. Proin condimentum fermentum nunc. Etiam pharetra, erat sed fermentum feugiat, velit mauris egestas quam, ut aliquam massa nisl quis neque. Suspendisse in orci enim. This is Mockup Studio's version of Lorem Ipsum. Proin gravida nibh vel velit auctor aliquet. Aenean sollicitudin, lorem quis bibendum auctor.</p>

<form class="order abs">
  <div class="order-head display">Order firewood</div>
  <p class="order-intro">Fill out the form below to order your firewood delivery. Deliveries are usually between <b>4:00PM &amp; 9:00PM</b> Can take up to 2 weeks to deliver (especially in the off session)</p>
  <div class="field" style="top:115px">Email <i>*</i></div>
  <div class="field" style="top:136px">Phone</div>
  <div class="field" style="top:157px">Address <i>*</i></div>
  <div class="field" style="top:178px">Zip Code/City <i>*</i></div>
  <div class="field" style="top:198px">Gate Code (if needed)</div>
  <div class="field select" style="top:219px">Firewood Type</div>
  <div class="field select" style="top:240px">Order Size</div>
  <div class="field select" style="top:261px">Kindling</div>
  <div class="next-btn display">Next
    <svg width="15" height="15" viewBox="0 0 15 15"><circle cx="7.5" cy="7.5" r="6.3" fill="none" stroke="#fff" stroke-width="1.8"/><path d="M4 7.5h6M7.5 4.8l2.8 2.7-2.8 2.7" fill="none" stroke="#fff" stroke-width="1.8"/></svg>
  </div>
</form>

<section class="products abs"></section>
<h2 class="products-title display abs">New products for <span>February</span></h2>
<div class="carousel-btn abs" style="left:86px"><svg width="8" height="8" viewBox="0 0 8 8"><path d="M5.5 1 2.5 4l3 3" fill="none" stroke="#fff" stroke-width="1.6"/></svg></div>
<div class="carousel-btn abs" style="left:711px"><svg width="8" height="8" viewBox="0 0 8 8"><path d="M2.5 1l3 3-3 3" fill="none" stroke="#fff" stroke-width="1.6"/></svg></div>
<article class="product abs" style="left:116px">
  <div class="photo" role="img" aria-label="Photo of a stack of split mixed hardwood" style="background:linear-gradient(135deg,#9a9a9a,#c9864a 50%,#6a4a30)"></div>
  <h3>MIXED HARDWOOD</h3><small>PICK-UP TRUCK LOAD</small><div class="price">$25.00</div>
</article>
<article class="product abs" style="left:264px">
  <div class="photo" role="img" aria-label="Photo of unsplit hardwood logs" style="background:linear-gradient(135deg,#5b4230,#b08258 50%,#4a3424)"></div>
  <h3>UNSPLIT WOOD</h3><small>STARTING AT</small><div class="price">$1.00 A LOG</div>
</article>
<article class="product abs" style="left:410px">
  <div class="photo" role="img" aria-label="Photo of a bunch of kindling sticks" style="background:linear-gradient(135deg,#c98a52,#e0a870 50%,#8a5630)"></div>
  <h3>BUNCH OF KINDLING</h3><small>1 FOR</small><div class="price">$10.00</div>
</article>
<article class="product abs" style="left:558px">
  <div class="photo" role="img" aria-label="Photo of plain wood mulch" style="background:linear-gradient(135deg,#8a8070,#b0a690 50%,#5a5040)"></div>
  <h3>PLAIN WOOD MULCH</h3><small>PICK-UP TRUCK LOAD</small><div class="price">$25.00</div>
</article>

<footer class="site-footer abs" role="img" aria-label="Dark background of glowing fire"></footer>
<h4 class="foot-title display abs" style="left:117px">Navigation</h4>
<ul class="foot-links abs" style="left:117px">
  <li>HOME</li><li>ABOUT US</li><li>OUR PRODUCTS</li><li>FIREWOOD</li><li style="border:0">FENCING</li>
</ul>
<ul class="foot-links abs" style="left:233px">
  <li style="width:88px">FENCING</li><li style="width:88px">CONTACT</li><li style="width:88px">CONDITIONS OF USE</li><li style="width:88px">PRIVACY POLICY</li>
</ul>
<h4 class="foot-title display abs" style="left:392px">Enquiry hotline</h4>
<div class="hotline abs">01632 960418<br>07700 900512</div>
<p class="areas abs">Our delivery areas include Boston, Grantham, King's Lynn, Lincoln, Louth, Melton Mowbray, Newark, Oakham, Peterborough and Wisbech</p>
<h4 class="foot-title display abs" style="left:586px">Hours:</h4>
<ul class="hours abs">
  <li>MON-THUR 8:00AM-8:00PM</li><li>FRIDAY 8:00AM-4:00PM</li><li>SATURDAY CLOSED ALL DAY</li><li>SUNDAY 8:00AM-7:00PM</li>
</ul>
<div class="foot-brand abs"><div class="dot"></div><p>Tall ridge firewood</p></div>
<p class="copyright abs">Copyrights © 2014, Tall ridge firewood. All rights Reserved</p>

</body>
</html>
```